BrightLedgerMoney(.com) needs website & logo design

We need our website mock-up made into a reality! We are wanting to launch a multifaceted website for all things financial - i.e. blogs, financial wellness information, and a network of redirect links.
We have an existing mock-up, which I will include, but are open to your creative approach!

Industry/Entity Type

Finance

Coding

Coded - Design and coding required

Number of Pages Required

1 page

Requirements
Must have
• Corresponding logo

```html
<!DOCTYPE html>
<html lang="en">
<head>
<meta charset="utf-8">
<title>Bright Ledger Money</title>
<link href="https://fonts.googleapis.com/css2?family=Barlow:wght@400;500&family=Roboto:wght@400;500&display=swap" rel="stylesheet">
<style>
:root{
  --purple:#a58fcb;
  --purple-dark:#9a82c4;
  --mint:#7ed8c3;
  --mint-soft:#b4eadb;
  --mint-frame:#cdf1e7;
  --lilac-bg:#ebe7f4;
  --ink:#222;
  --body:#3a3a3a;
  --white:#fff;
}
*{margin:0;padding:0;box-sizing:border-box}
html,body{width:1200px;height:3447px;overflow:hidden;background:var(--white)}
body{position:relative;font-family:'Roboto',sans-serif;color:var(--body)}
.abs{position:absolute}
h1,h2,h3{font-family:'Barlow',sans-serif;font-weight:400;color:var(--ink)}
.rule{position:absolute;height:3px;background:var(--purple)}
.btn{position:absolute;display:flex;align-items:center;justify-content:center;color:var(--white);font-size:15px;border-radius:5px}
.btn.mint{background:var(--mint)}
.btn.purple{background:var(--purple)}
.photo{position:absolute}

/* hero */
.hero{position:absolute;left:0;top:0;width:1200px;height:471px;background:linear-gradient(100deg,#4f5a3c 0%,#8a8b64 35%,#b89b78 60%,#6d7a52 85%,#3f4a33 100%)}
.site-brand{position:absolute;left:113px;top:26px;font-family:'Barlow',sans-serif;font-size:33px;line-height:42px;color:var(--white);white-space:nowrap}
.menu{left:1058px;top:32px;width:30px;height:30px;border:1.5px solid var(--white);border-radius:50%}
.hero-panel{left:112px;top:123px;width:530px;height:285px;background:linear-gradient(90deg,rgba(165,143,203,.92),rgba(165,143,203,.55) 75%,rgba(165,143,203,0));border-left:3px solid rgba(200,190,230,.8);border-top:2px solid rgba(200,190,230,.6)}
.hero-panel h1{position:absolute;left:42px;top:40px;font-size:34px;line-height:42px;font-weight:500;color:var(--white);white-space:nowrap}
.hero-panel .kicker{position:absolute;left:42px;top:96px;font-size:16px;line-height:20px;color:var(--white);white-space:nowrap}
.hero-panel .lede{position:absolute;left:42px;top:124px;width:470px;font-size:17px;line-height:30px;color:var(--white)}
.hero-panel .signup{position:absolute;left:42px;top:205px;font-family:'Barlow',sans-serif;font-weight:500;font-size:25px;line-height:30px;color:var(--white);white-space:nowrap}
.email-field{left:157px;top:381px;width:216px;height:45px;background:var(--white);border-radius:4px;font-size:15px;color:#333;display:flex;align-items:center;padding-left:27px}

/* feature tiles */
.tiles{position:absolute;left:0;top:471px;width:1200px;height:174px;display:flex}
.tile{width:200px;height:174px;display:flex;flex-direction:column;align-items:center;padding-top:34px;color:var(--white);font-size:17px;font-weight:500}
.tile:nth-child(odd){background:var(--purple)}
.tile:nth-child(even){background:var(--mint)}
.tile svg{width:66px;height:66px;margin-bottom:12px;fill:none;stroke:var(--white);stroke-width:2.4;stroke-linecap:round;stroke-linejoin:round}

/* text blocks */
.section-title{position:absolute;font-size:37px;line-height:50px;white-space:nowrap}
.copy{position:absolute;font-size:17px;line-height:29px;color:var(--body)}
.copy p+p{margin-top:18px}

/* offers */
.offers{position:absolute;left:0;top:1232px;width:1200px;height:570px;background:var(--lilac-bg)}
.card{position:absolute;width:276px;height:166px;background:var(--white);border:1px solid #ddd;border-radius:6px;padding:24px 22px}
.card .head{display:flex;align-items:center;gap:8px;font-size:17px;font-weight:500;color:#222;height:44px;white-space:nowrap}
.card .ico{width:42px;height:42px;flex:none;border-radius:50%;display:flex;align-items:center;justify-content:center}
.card .ico svg{width:30px;height:30px;fill:none;stroke-width:2;stroke-linecap:round;stroke-linejoin:round}
.ico.m{background:#d7f2ea}.ico.m svg{stroke:#4fbfa2}
.ico.p{background:#e2dbef}.ico.p svg{stroke:#8c74ba}
.card p{margin-top:12px;font-size:15px;line-height:26px;color:#3a3a3a}

/* blog */
.post{position:absolute;top:2376px;width:292px}
.post .thumb{width:291px;height:194px;border-radius:40px 0 40px 0}
.post h3{margin-top:38px;font-family:'Roboto',sans-serif;font-weight:500;font-size:19px;line-height:25px;color:#222}
.post p{margin-top:12px;font-size:14px;line-height:28px;color:#3a3a3a}
.post a{display:inline-block;margin-top:10px;font-size:14px;color:#222;text-decoration:underline}

/* contact band */
.questions{position:absolute;left:0;top:2835px;width:1200px;height:353px;background:var(--mint-soft)}

/* footer */
.foot-brand{left:113px;top:3228px;font-family:'Barlow',sans-serif;font-size:34px;line-height:42px;color:var(--purple);white-space:nowrap}
.social{position:absolute;top:3299px;width:42px;height:42px;border:2px solid var(--mint);border-radius:50%}
.links-title{left:585px;top:3234px;font-size:15px;color:var(--purple)}
.links{position:absolute;left:590px;top:3264px;list-style:none;font-size:15px;color:#222;line-height:30px}
.contact-label{font-size:16px;letter-spacing:.5px;color:#222}
.contact-value{font-size:15px;color:#222;white-space:nowrap}
.contact-ico{position:absolute;width:22px;height:22px;fill:none;stroke:#b9a9d9;stroke-width:1.6;stroke-linecap:round;stroke-linejoin:round}
.copyright{left:0;top:3412px;width:1200px;text-align:center;font-size:14px;color:#222}
</style>
</head>
<body>

<header class="hero" role="img" aria-label="Photo of stacked coins with sprouting plants and a small wooden house"></header>
<div class="site-brand">Bright Ledger Money</div>
<div class="abs menu">
  <svg width="27" height="27" viewBox="0 0 27 27"><path d="M8 9.5h11M8 13.5h11M8 17.5h11" stroke="#fff" stroke-width="1.6"/></svg>
</div>

<section class="abs hero-panel">
  <h1>A Clear path to financial wellness</h1>
  <div class="kicker">Trending in 202: Financial Literacy</div>
  <div class="lede">Having insight to relevant information is what we bring to the table in a clear and easy to digest way.</div>
  <div class="signup">Signup for free</div>
</section>
<div class="abs email-field">Your Email</div>
<div class="btn mint" style="left:381px;top:381px;width:131px;height:45px">Get Started</div>

<nav class="tiles">
  <div class="tile">
    <svg viewBox="0 0 66 66"><circle cx="33" cy="26" r="10"/><path d="M33 20v12M30 23h5a2 2 0 010 4h-4a2 2 0 000 4h5"/><path d="M33 6v5M25 9l2 4M41 9l-2 4"/><path d="M8 48l10-6h10l8 4h8M12 58l12-4 18 2 16-12"/></svg>
    Save</div>
  <div class="tile">
    <svg viewBox="0 0 66 66"><path d="M30 10a22 22 0 1022 22H30z"/><path d="M36 6a22 22 0 0120 20H36z"/><circle cx="18" cy="38" r="8"/><circle cx="18" cy="48" r="8"/></svg>
    Budget</div>
  <div class="tile">
    <svg viewBox="0 0 66 66"><rect x="6" y="6" width="54" height="54" rx="5"/><path d="M33 6v54M6 33h54M14 20h12M20 14v12M40 20h12M15 41l10 10M25 41l-10 10M40 44h12M40 50h12"/></svg>
    Calculate</div>
  <div class="tile">
    <svg viewBox="0 0 66 66"><path d="M6 58h54M12 58V44h8v14M26 58V38h8v14M40 58V30h8v28M6 40l14-8 14 4 16-14"/><circle cx="52" cy="12" r="8"/></svg>
    Track</div>
  <div class="tile">
    <svg viewBox="0 0 66 66"><circle cx="26" cy="26" r="18"/><circle cx="26" cy="26" r="12"/><path d="M40 40l18 18"/></svg>
    Research</div>
  <div class="tile">
    <svg viewBox="0 0 66 66"><circle cx="33" cy="16" r="10"/><path d="M33 26v34M33 46c-8 0-16-6-16-14 8 0 16 6 16 14zM33 40c8 0 16-6 16-14-8 0-16 6-16 14z"/></svg>
    Invest</div>
</nav>

<!-- trending -->
<h2 class="section-title" style="left:112px;top:740px">Trending in 2021:<br>Financial Literacy</h2>
<div class="rule" style="left:112px;top:855px;width:110px"></div>
<div class="copy" style="left:112px;top:888px;width:520px">
  <p>Lorem ipsum dolor sit amet, consectetur adipiscing elit, sed do eiusmod tempor incididunt ut labore et dolore aliqua. Quis ipsum suspendisse ultrices gravida. Risus commodo viverra maecenas accumsan lacus vel facilisis.</p>
  <p>Quis ipsum suspendisse ultrices gravida. Risus commodo viverra maecenas accumsan lacus vel facilisis.</p>
</div>
<div class="btn mint" style="left:112px;top:1107px;width:133px;height:45px">Learn More</div>
<div class="abs" style="left:776px;top:743px;width:330px;height:401px;background:var(--mint-frame);border-radius:0 60px 0 0"></div>
<div class="photo" role="img" aria-label="Photo of a smiling couple reviewing paperwork together" style="left:758px;top:759px;width:331px;height:400px;background:linear-gradient(160deg,#6a5648,#a59486 45%,#d9d4cf 100%);border-radius:0 60px 0 60px"></div>

<!-- offers -->
<section class="offers">
  <h2 class="section-title" style="left:0;width:1200px;text-align:center;top:50px">What we offer</h2>
  <div class="rule" style="left:545px;top:105px;width:110px"></div>
</section>

<div class="card" style="left:114px;top:1385px">
  <div class="head"><span class="ico m"><svg viewBox="0 0 30 30"><circle cx="14" cy="16" r="10"/><circle cx="14" cy="16" r="5"/><path d="M14 16l12-12M22 4h4v4"/></svg></span>Set Goals</div>
  <p>Duis aute irure dolo reprehenderit in voluptate velit ese cillum.</p>
</div>
<div class="card" style="left:400px;top:1385px">
  <div class="head"><span class="ico p"><svg viewBox="0 0 30 30"><circle cx="15" cy="15" r="11"/><path d="M15 8v14M18 11h-4a2 2 0 000 4h2a2 2 0 010 4h-4"/></svg></span>Money 101</div>
  <p>Duis aute irure dolo reprehenderit in voluptate velit ese cillum.</p>
</div>
<div class="card" style="left:688px;top:1385px">
  <div class="head"><span class="ico m"><svg viewBox="0 0 30 30"><path d="M14 6a10 10 0 1010 10H14z"/><path d="M17 3a10 10 0 019 9h-9z"/></svg></span>Budgeting</div>
  <p>Duis aute irure dolo reprehenderit in voluptate velit ese cillum.</p>
</div>
<div class="card" style="left:241px;top:1561px">
  <div class="head"><span class="ico p"><svg viewBox="0 0 30 30"><rect x="4" y="8" width="22" height="15" rx="2"/><path d="M4 13h22M8 19h6"/></svg></span>Credit Mindfulness</div>
  <p>Duis aute irure dolo reprehenderit in voluptate velit ese cillum.</p>
</div>
<div class="card" style="left:527px;top:1561px">
  <div class="head"><span class="ico m"><svg viewBox="0 0 30 30"><path d="M6 12h18l-2 14H8zM11 12V8a4 4 0 018 0v4M15 15v8M17 17h-3a1.5 1.5 0 000 3h2a1.5 1.5 0 010 3h-3"/></svg></span>Debt Management</div>
  <p>Duis aute irure dolo reprehenderit in voluptate velit ese cillum.</p>
</div>
<div class="card" style="left:815px;top:1561px">
  <div class="head"><span class="ico p"><svg viewBox="0 0 30 30"><rect x="5" y="4" width="15" height="20" rx="2"/><path d="M9 10h7M9 14h7"/><circle cx="22" cy="22" r="5"/></svg></span>Retirement Planning</div>
  <p>Duis aute irure dolo reprehenderit in voluptate velit ese cillum.</p>
</div>

<!-- wellness -->
<div class="abs" style="left:127px;top:1896px;width:332px;height:308px;background:var(--mint-frame);border-radius:0 60px 0 60px"></div>
<div class="photo" role="img" aria-label="Photo of a person writing notes beside a laptop showing financial charts" style="left:111px;top:1879px;width:331px;height:313px;background:linear-gradient(135deg,#3d4552,#7e8896 50%,#c7cdd6);border-radius:0 60px 0 60px"></div>
<h2 class="section-title" style="left:575px;top:1896px">Financial Wellness 101</h2>
<div class="rule" style="left:575px;top:1961px;width:110px"></div>
<div class="copy" style="left:575px;top:1991px;width:520px">
  <p>Lorem ipsum dolor sit amet, consectetur adipiscing elit, sed do eiusmod tempor incididunt ut labore et dolore aliqua. Quis ipsum suspendisse ultrices gravida. Risus commodo viverra maecenas accumsan lacus vel facilisis.</p>
</div>
<div class="btn purple" style="left:575px;top:2130px;width:132px;height:46px">Learn More</div>

<!-- blog -->
<h2 class="section-title" style="left:0;width:1200px;text-align:center;top:2272px">Latest Blog</h2>
<div class="rule" style="left:545px;top:2338px;width:110px"></div>

<article class="post" style="left:114px">
  <div class="thumb" role="img" aria-label="Photo of hands reviewing charts on a tablet" style="background:linear-gradient(135deg,#2f4a6e,#7c95b5 55%,#d6dde8)"></div>
  <h3>Ut enim ad minima veniam, quis nostrum</h3>
  <p>Enim ad minima veniam, quis nostrum Ut enim ad minima veniaquis nostrum Ut enim ad minima veniam.</p>
  <a>Read More</a>
</article>
<article class="post" style="left:455px">
  <div class="thumb" role="img" aria-label="Photo of a coin being dropped into a piggy bank" style="background:linear-gradient(160deg,#3a3f4a,#8c8a86 55%,#e6ddd2)"></div>
  <h3>Ut enim ad minima veniam, quis nostrum</h3>
  <p>Enim ad minima veniam, quis nostrum Ut enim ad minima veniaquis nostrum Ut enim ad minima veniam.</p>
  <a>Read More</a>
</article>
<article class="post" style="left:797px">
  <div class="thumb" role="img" aria-label="Photo of a woman smiling at her phone in an office" style="background:linear-gradient(135deg,#c9ccc8,#8f918c 50%,#2c2c2e)"></div>
  <h3>Ut enim ad minima veniam, quis nostrum</h3>
  <p>Enim ad minima veniam, quis nostrum Ut enim ad minima veniaquis nostrum Ut enim ad minima veniam.</p>
  <a>Read More</a>
</article>

<!-- questions -->
<section class="questions">
  <h2 class="section-title" style="left:0;width:1200px;text-align:center;top:50px">Have Any Questions?</h2>
  <div class="rule" style="left:545px;top:113px;width:110px"></div>
  <p class="copy" style="left:225px;width:750px;text-align:center;top:146px">Lorem ipsum dolor sit amet, consectetur adipiscing elit, sed do eiusmod tempor incididunt ut labore et dolore aliqua. Quis ipsum suspendisse ultrices gravida. Risus commodo viverra maecenas accumsan lacus vel facilisis.</p>
  <div class="btn purple" style="left:534px;top:254px;width:131px;height:46px">Contact Us</div>
</section>

<!-- footer -->
<footer>
  <div class="abs foot-brand">Bright Ledger Money</div>
  <span class="social" style="left:111px" aria-label="Social profile"></span>
  <span class="social" style="left:164px" aria-label="Social profile"></span>
  <span class="social" style="left:217px" aria-label="Social profile"></span>
  <span class="social" style="left:269px" aria-label="Social profile"></span>
  <span class="social" style="left:322px" aria-label="Social profile"></span>

  <div class="abs links-title">QUICK LINKS</div>
  <ul class="links"><li>Home</li><li>About</li><li>Latest Stories</li><li>Contact</li></ul>

  <svg class="contact-ico" style="left:860px;top:3245px" viewBox="0 0 22 22"><path d="M5 2l4 4-2 3c1 3 4 6 7 7l3-2 4 4-3 3C10 20 2 12 2 5z"/></svg>
  <div class="abs" style="left:900px;top:3236px">
    <div class="contact-label">PHONE</div>
    <div class="contact-value">+1-800-555-0142</div>
  </div>
  <svg class="contact-ico" style="left:862px;top:3314px" viewBox="0 0 22 22"><rect x="1" y="5" width="20" height="13"/><path d="M1 5l10 8 10-8"/></svg>
  <div class="abs" style="left:902px;top:3306px">
    <div class="contact-label">EMAIL</div>
    <div class="contact-value">info@brightledgermoney.com</div>
  </div>

  <div class="abs copyright">2023 Bright Ledger Money. All Rights Reserved.</div>
</footer>

</body>
</html>
```